Under Morning Lantern website

I need a website to sell my t-shirt designs. I have around 5 designs I plan to sell on my initial launch, but only 3 photos at the moment. I would love a main page with the product images below maybe a large nicely designed header image, showing products with their sizes, item name/description, a way to add to cart and a review system like stars below each product image. Maybe a share option to Instagram, Share, Tweet, Pin it, etc. would be cool too. Also on the main page under the product images a section showcasing my Instagram photos for the company. Then a section where I will include an About Me video from like YouTube. Lastly, on the main page an option to join my Mailing List at the footer with links to my Share and Instagram social accounts, links to pages (About Me, Shop, Instagram page, & Contact Us) as well as Track Order.

The other 4 pages will be for an About Me, which is the video I will make later that will be from YouTube. Then the Shop page. Then the Instagram page showcasing all the photos I plan to use to market the products, and a Contact Us Page.

I plan to possibly connect this to Shopify, so showcasing payment options (Palo, Birch Pay, Wayfarer, etc.) would be nice.

Lastly, I don't plan on doing returns/exchanges so maybe an area showing that would be nice too. ALL SALES FINAL

Mobile Friendly!

1st image is logo and other 4 images are t-shirt designs

Coded - Design and coding required

5+ page

• Separate pages, No Refunds (All Sales Final), Add to Cart, Way to Purchase

```html
<!DOCTYPE html>
<html lang="en">
<head>
<meta charset="utf-8">
<title>Under Morning Lantern — Home</title>
<link href="https://fonts.googleapis.com/css2?family=Lato:wght@400;700;900&family=Oswald:wght@400;500&display=swap" rel="stylesheet">
<style>
:root{
  --blue:#1e90e6;
  --ink:#1d1d1d;
  --body:#444;
  --muted:#777;
  --rule:#d9d9d9;
  --star:#f0592a;
  --white:#fff;
  --orange:#fb4f24;
  --purple:#8047c6;
  --yellow:#ffef00;
  --teal:#23a99d;
  --grey:#c9c9c9;
}
*{box-sizing:border-box;margin:0;padding:0}
html,body{width:1200px;height:3677px;overflow:hidden;background:var(--white)}
body{position:relative;font-family:'Lato',sans-serif;color:var(--ink)}
.abs{position:absolute}

/* header */
.site-header{position:absolute;left:0;top:0;width:1200px;height:106px;background:var(--white)}
.brand{left:75px;top:22px;color:var(--blue);font-weight:900;line-height:1}
.brand-initials{font-size:46px;letter-spacing:1px;display:block}
.brand-name{font-size:8.5px;letter-spacing:1.6px;display:block;margin-top:4px}
.nav{left:532px;top:34px;display:flex;align-items:center;height:40px}
.nav a{font-size:13px;color:var(--ink);text-decoration:none;text-transform:uppercase;margin-right:39px}
.nav a.active{background:var(--blue);color:var(--white);padding:0 20px;height:40px;line-height:40px}
.icons{left:1050px;top:44px;display:flex;gap:40px}

/* hero */
.hero{left:0;top:106px;width:1200px;height:632px;background:linear-gradient(100deg,#4a4a48 0%,#6b6a66 45%,#8d8b86 100%)}
.hero-title{left:75px;top:322px;font-size:57px;font-weight:700;color:var(--white);letter-spacing:.5px;line-height:1.1}
.hero-sub{left:75px;top:390px;font-size:24px;color:var(--white)}
.btn{background:var(--blue);color:var(--white);font-weight:700;text-align:center;text-transform:uppercase}
.hero-btn{left:76px;top:461px;width:179px;height:47px;line-height:47px;font-size:16px}
.dots{display:flex;gap:7px}
.dot{width:10px;height:10px;border-radius:50%;background:var(--white)}
.dot.on{background:var(--blue)}

/* sections */
.h2{font-size:28px;font-weight:400;text-transform:uppercase;letter-spacing:.3px;color:var(--ink)}
.copy{font-size:13.5px;line-height:24px;color:var(--body)}

.play{left:838px;top:1013px;width:64px;height:64px;border-radius:50%;background:var(--white)}

.price-old{font-family:'Oswald',sans-serif;font-size:24px;color:var(--muted);text-decoration:line-through}
.price-new{font-family:'Oswald',sans-serif;font-size:24px;color:var(--blue);margin-left:12px}
.select{left:641px;top:1477px;width:137px;height:43px;border:1px solid var(--rule);font-size:12px;padding:0 14px;display:flex;align-items:center;justify-content:space-between;color:var(--ink)}
.add-btn{left:641px;top:1543px;width:332px;height:40px;line-height:40px;font-size:13px}
.shares{left:641px;top:1754px;display:flex;gap:5px}
.share{border:1px solid var(--rule);height:30px;padding:0 10px;font-size:11px;line-height:28px;text-transform:uppercase;color:var(--body);display:flex;align-items:center;gap:6px}
.share i{width:8px;height:8px;background:var(--muted);display:block}

.card{width:320px;text-align:center}
.card .shot{width:240px;height:309px;margin:0 auto}
.card .name{font-size:16px;margin-top:30px}
.card .rating{font-size:13px;color:var(--muted);margin-top:6px}
.card .rating b{color:var(--star);letter-spacing:3px;font-size:14px;margin-right:6px}
.card .price{font-size:17px;margin-top:14px}
.card .dots{justify-content:center;margin-top:22px;gap:12px}
.card .dot{width:9px;height:9px}

.insta{top:3078px;width:252px;height:233px}

/* footer */
.f-head{font-size:18px;font-weight:400;color:var(--ink);text-transform:uppercase;letter-spacing:.3px}
.f-links{left:75px;top:3438px;display:flex;gap:32px;font-size:14px;color:var(--body)}
.email{left:705px;top:3440px;width:277px;height:48px;border:1px solid var(--rule);border-right:0;font-size:13px;padding-left:12px;line-height:46px;color:var(--ink)}
.signup{left:982px;top:3440px;width:144px;height:48px;line-height:48px;font-family:'Oswald',sans-serif;font-weight:400;font-size:20px}
.rule{left:75px;top:3542px;width:1051px;height:1px;background:var(--rule)}
.copyright{left:75px;top:3592px;font-size:13px;color:var(--body)}
.pay{left:822px;top:3587px;display:flex;gap:6px}
.pay span{width:45px;height:27px;border:1px solid var(--rule);border-radius:3px;font-size:8.5px;font-weight:700;display:flex;align-items:center;justify-content:center;color:#3a4a7a;background:#f4f6fa}
</style>
</head>
<body>

<header class="site-header">
  <div class="abs brand"><span class="brand-initials">U.M.L.</span><span class="brand-name">UNDER MORNING LANTERN</span></div>
  <nav class="abs nav">
    <a class="active" href="#">Home</a><a href="#">Products</a><a href="#">Shop</a><a href="#">Blog</a><a href="#">Contact us</a>
  </nav>
  <div class="abs icons">
    <svg width="18" height="18" viewBox="0 0 18 18" aria-label="Search"><circle cx="7.5" cy="7.5" r="5.5" fill="none" stroke="#222" stroke-width="2.4"/><line x1="11.5" y1="11.5" x2="16" y2="16" stroke="#222" stroke-width="2.6" stroke-linecap="round"/></svg>
    <svg width="18" height="18" viewBox="0 0 18 18" aria-label="Cart"><path d="M1 3h3l2 8h9l2-6H5" fill="none" stroke="#222" stroke-width="2"/><path d="M5 5h12l-2 6H6z" fill="#222"/><circle cx="7" cy="15" r="1.6" fill="#222"/><circle cx="14" cy="15" r="1.6" fill="#222"/></svg>
  </div>
</header>

<section class="abs hero" role="img" aria-label="Man wearing a white logo t-shirt in front of stone steps"></section>
<h1 class="abs hero-title">WELCOME TO U.M.L.</h1>
<p class="abs hero-sub">Vestibulum ante ipsum primis in faucibus</p>
<div class="abs btn hero-btn">Shop now</div>
<div class="abs dots" style="left:568px;top:681px"><i class="dot on"></i><i class="dot"></i><i class="dot"></i><i class="dot"></i></div>

<h2 class="abs h2" style="left:75px;top:962px">About me</h2>
<p class="abs copy" style="left:76px;top:1012px;width:515px;line-height:27.5px">Duis facilisis efficitur massa, eu elementum urna. Donec sed ultricies tortor. Etiam eu quam id ante sollicitudin porta. Aenean dignissim pretium accumsan. Interdum et malesuada fames ac ante ipsum primis in faucibus. Ut iaculis purus vel mi consectetur egestas.</p>
<div class="abs" style="left:614px;top:816px;width:512px;height:456px;background:linear-gradient(135deg,#5b4331,#8a7766 40%,#e2e2e2 50%,#8a7766 62%,#4a3a2f)" role="img" aria-label="About me video: white logo t-shirt laid flat with winter clothes"></div>
<div class="abs play"><svg width="64" height="64" viewBox="0 0 64 64"><path d="M25 19l22 13-22 13z" fill="#555"/></svg></div>

<div class="abs" style="left:76px;top:1356px;width:512px;height:455px;background:linear-gradient(90deg,var(--orange) 0%,var(--purple) 12%,var(--purple) 44%,#111 46%,#111 88%,var(--orange) 100%)" role="img" aria-label="Purple and black logo t-shirts hanging on an orange wall"></div>
<h2 class="abs h2" style="left:639px;top:1373px">Featured product</h2>
<div class="abs" style="left:639px;top:1420px"><span class="price-old">$19.99</span><span class="price-new">$17.99</span></div>
<div class="abs select"><span>Select Color</span><svg width="8" height="6" viewBox="0 0 8 6"><path d="M1 1l3 3 3-3" fill="none" stroke="#444" stroke-width="1.3"/></svg></div>
<div class="abs btn add-btn">Add to cart</div>
<p class="abs copy" style="left:641px;top:1600px;width:480px">Aliquam molestie, mi et imperdiet euismod, dui purus auctor tellus, et interdum lacus lectus et ante. Sed accumsan sollicitudin sapien, sit amet adipiscing turpis gravida ac. In congue, neque ac lobortis volutpat, libero mauris varius mi, vitae suscipit ipsum ligula vitae risus ante ipsum primis in faucibus orci luctus et ultrices posuere cubilia..</p>
<div class="abs shares"><span class="share"><i></i>Share</span><span class="share"><i></i>Tweet</span><span class="share"><i></i>Pin it</span></div>

<h2 class="abs h2" style="left:0;top:1935px;width:1200px;text-align:center">Featured collections</h2>
<div class="abs card" style="left:80px;top:2010px">
  <div class="shot" role="img" aria-label="White logo t-shirt on a hanger" style="background:radial-gradient(ellipse at 50% 60%,#d4d4d4 0%,#e6e6e6 55%,#fff 72%)"></div>
  <div class="name">Product Name</div><div class="rating"><b>★★★★★</b>1 review</div><div class="price">$15.00</div>
  <div class="dots"><i class="dot" style="background:#ddd"></i><i class="dot" style="background:#111"></i></div>
</div>
<div class="abs card" style="left:440px;top:2010px">
  <div class="shot" role="img" aria-label="Black slogan t-shirt on a hanger" style="background:radial-gradient(ellipse at 50% 60%,#111 0%,#1a1a1a 55%,#fff 72%)"></div>
  <div class="name">Product Name</div><div class="rating"><b>★★★★★</b>1 review</div><div class="price">$15.00</div>
  <div class="dots"><i class="dot" style="background:var(--teal)"></i><i class="dot" style="background:#111"></i></div>
</div>
<div class="abs card" style="left:800px;top:2010px">
  <div class="shot" role="img" aria-label="Teal slogan t-shirt on a hanger" style="background:radial-gradient(ellipse at 50% 60%,#1f9c91 0%,var(--teal) 55%,#fff 72%)"></div>
  <div class="name">Product Name</div><div class="rating"><b>★★★★★</b>1 review</div><div class="price">$15.00</div>
  <div class="dots"><i class="dot" style="background:var(--teal)"></i><i class="dot" style="background:#111"></i></div>
</div>

<div class="abs" style="left:0;top:2537px;width:600px;height:396px;background:linear-gradient(90deg,#b9b2aa 0%,#9d948a 45%,#e8e8e8 55%,#e8e8e8 68%,#8c8072 80%)" role="img" aria-label="Man in a white logo t-shirt on a city street"></div>
<div class="abs" style="left:600px;top:2537px;width:600px;height:396px;background:linear-gradient(90deg,#6e8494 0%,#3d5a6e 25%,#14181e 40%,#14181e 70%,#52606a 100%)" role="img" aria-label="Woman in a black logo t-shirt against a painted wall"></div>

<h2 class="abs h2" style="left:0;top:2995px;width:1200px;text-align:center">Instagram feeds</h2>
<div class="abs insta" style="left:75px;background:linear-gradient(90deg,var(--orange) 5%,var(--purple) 6%,var(--purple) 46%,#111 54%,#111 94%,var(--orange) 95%)" role="img" aria-label="Purple and black t-shirts on orange"></div>
<div class="abs insta" style="left:341px;background:linear-gradient(90deg,var(--grey) 5%,#f2f2f2 6%,#f2f2f2 46%,var(--grey) 50%,#f2f2f2 54%,#f2f2f2 94%,var(--grey) 95%)" role="img" aria-label="Two white t-shirts on grey"></div>
<div class="abs insta" style="left:608px;background:linear-gradient(90deg,var(--purple) 5%,#f2f2f2 6%,#f2f2f2 46%,#111 54%,#111 94%,var(--purple) 95%)" role="img" aria-label="White and black t-shirts on purple"></div>
<div class="abs insta" style="left:873px;background:linear-gradient(90deg,var(--yellow) 5%,var(--teal) 6%,var(--teal) 46%,#111 54%,#111 94%,var(--yellow) 95%)" role="img" aria-label="Teal and black t-shirts on yellow"></div>

<h3 class="abs f-head" style="left:75px;top:3398px">Quick links</h3>
<div class="abs f-links"><span>Search</span><span>About Us</span><span>Contact us</span></div>
<h3 class="abs f-head" style="left:705px;top:3398px">Sign up for our newsletter</h3>
<div class="abs email">Enter Email Address</div>
<div class="abs btn signup">SIGN UP</div>
<div class="abs rule"></div>
<p class="abs copyright">Copyright © 2020. Company Name. All Right Reserved</p>
<div class="abs pay"><span>Palo</span><span>Meridian</span><span>Amberline</span><span>Parcelo</span><span>Dinely</span><span>Wayfarer</span></div>

</body>
</html>
```